SkyvornQ Business Cards and Stationary Design

Need a design for our business cards and stationary. I want to carry on the theme of the logo. I want the business cards to have a design on the back. I would like the business cards and the stationary to carry the same theme, design scheme, and branding

Target Market(s)

Airlines and Maintenance Facilities

Industry/Entity Type

Aviation

Contact Information for Business Card

Name
Position Title
Address: 4827 Trellis Hollow Road, Marlow Bay, Oregon, 97421
Office Number
Mobile Number
Email
Website

Font styles to use
Serif
Sans Serif

Colors

Designer to choose colors to be used in the design.

```html
<!DOCTYPE html>
<html lang="en">
<head>
<meta charset="utf-8">
<title>SkyvornQ Business Card</title>
<link href="https://fonts.googleapis.com/css2?family=Open+Sans:wght@400;600;700&display=swap" rel="stylesheet">
<style>
  :root {
    --bg: #e4e4e4;
    --navy: #152b52;
    --navy-soft: #1f3b6a;
    --sky: #1b93d8;
    --paper: #f7f7f7;
    --ink: #1d2f55;
  }
  * { box-sizing: border-box; margin: 0; padding: 0; }
  html, body {
    width: 1200px; height: 852px; overflow: hidden;
    background: var(--bg);
    font-family: "Open Sans", Arial, sans-serif;
  }
  .stage { position: relative; width: 1200px; height: 852px; }
  .card {
    position: absolute; top: 281px;
    width: 500px; height: 290px;
    border-radius: 18px; overflow: hidden;
  }
  .card-back { left: 70px; background: var(--navy); }
  .card-front { left: 630px; background: var(--paper); }

  .brand { display: flex; align-items: center; gap: 12px; position: absolute; }
  .brand-dot { border-radius: 50%; flex: none; }
  .brand-name { font-weight: 700; letter-spacing: 3px; text-transform: uppercase; line-height: 1; }

  .card-back .brand { left: 50%; top: 50%; transform: translate(-50%, -50%); }
  .card-back .brand-dot { width: 46px; height: 46px; border: 4px solid var(--navy-soft); }
  .card-back .brand-name { font-size: 38px; color: var(--navy-soft); }

  .card-front .brand { left: 34px; top: 118px; }
  .card-front .brand-dot { width: 40px; height: 40px; border: 4px solid var(--sky); }
  .card-front .brand-name { font-size: 28px; color: var(--navy); }

  .contact { position: absolute; left: 290px; top: 48px; color: var(--ink); }
  .contact-name { font-size: 21px; font-weight: 600; color: var(--sky); line-height: 1.1; }
  .contact-title { font-size: 11.5px; margin-bottom: 18px; }
  .contact-list { list-style: none; font-size: 11.5px; line-height: 16px; }
  .contact-list li { display: flex; align-items: flex-start; gap: 8px; }
  .contact-list svg { width: 10px; height: 10px; margin-top: 3px; fill: var(--ink); flex: none; }
  .contact-list .no-icon { padding-left: 18px; }

  .band { position: absolute; left: 0; bottom: 0; width: 500px; height: 60px; }
  .band-web {
    position: absolute; right: 26px; bottom: 16px;
    color: #fff; font-size: 12px; letter-spacing: 0.3px;
  }
</style>
</head>
<body>
<main class="stage">
  <section class="card card-back" aria-label="Card back">
    <div class="brand">
      <span class="brand-dot"></span>
      <span class="brand-name">SkyvornQ</span>
    </div>
  </section>

  <section class="card card-front" aria-label="Card front">
    <div class="brand">
      <span class="brand-dot"></span>
      <span class="brand-name">SkyvornQ</span>
    </div>

    <div class="contact">
      <p class="contact-name">Marcus Dellwyn</p>
      <p class="contact-title">Managing Director</p>
      <ul class="contact-list">
        <li><svg viewBox="0 0 10 10"><path d="M1 3 Q5 0 9 3 L8 4.5 L6.5 3.8 L6.5 3 Q5 2.5 3.5 3 L3.5 3.8 L2 4.5 Z M2.5 5 H7.5 L8.5 9 H1.5 Z"/></svg>555 0142 300</li>
        <li><svg viewBox="0 0 10 10"><path d="M3 0 H7 Q8 0 8 1 V9 Q8 10 7 10 H3 Q2 10 2 9 V1 Q2 0 3 0 Z M3 1.5 V7.5 H7 V1.5 Z"/></svg>555 0198 417</li>
        <li><svg viewBox="0 0 10 10"><path d="M0 2 H10 V8 H0 Z M0.8 2.6 L5 5.6 L9.2 2.6 V3.6 L5 6.6 L0.8 3.6 Z" fill-rule="evenodd"/></svg>marcus@skyvornq.com</li>
        <li class="no-icon">4827 Trellis Hollow Road,</li>
        <li class="no-icon">Marlow Bay, Oregon, 97421</li>
      </ul>
    </div>

    <svg class="band" viewBox="0 0 500 60" aria-hidden="true">
      <path d="M0 50 L300 24 L300 36 L0 60 Z" fill="var(--sky)"/>
      <path d="M285 60 L285 30 Q285 10 305 10 L500 10 L500 60 Z" fill="var(--navy)"/>
    </svg>
    <span class="band-web">www.skyvornq.com</span>
  </section>
</main>
</body>
</html>
```